Business card por a urban DJ, up scale audience target

Need a sober design, modern, conservative colors but i can consider some options, y play rnb, hip hop, EDM and top40.

Business card for contact and personal info, double sided, use logo attrached please; im 42 so i need a card acording to my age an target audience.

Target Market(s)

Adult people, up scale audience

Industry/Entity Type

Music Download

Contact Information for Business Card

Cel (318) 4207265518 www.lumadrift.com

Requirements
Must have
• open mind
Nice to have
• open mind
Should not have
• DJ

```html
<!DOCTYPE html>
<html lang="en">
<head>
<meta charset="utf-8">
<title>Lumadrift Business Card</title>
<link href="https://fonts.googleapis.com/css2?family=Jost:wght@400;500;600;700&display=swap" rel="stylesheet">
<style>
  :root {
    --backdrop: #3b3d40;
    --card-light: #fbfbfb;
    --card-dark: #1b1b1b;
    --ink: #1c1c1c;
    --ink-soft: #8a8a8a;
    --ink-mid: #444444;
    --paper-ink: #f2f2f2;
    --rule: #bdbdbd;
  }
  * { margin: 0; padding: 0; box-sizing: border-box; }
  html, body { width: 1200px; height: 750px; overflow: hidden; }
  body {
    background: var(--backdrop);
    font-family: "Jost", "Futura", sans-serif;
    position: relative;
  }
  .card {
    position: absolute;
    top: 228px;
    width: 462px;
    height: 263px;
    box-shadow: 0 4px 10px rgba(0,0,0,0.45);
  }
  .card--front { left: 124px; background: var(--card-light); color: var(--ink); }
  .card--back { left: 618px; background: var(--card-dark); color: var(--paper-ink); }

  .wordmark {
    position: absolute;
    left: 0; right: 0;
    display: flex;
    align-items: center;
    justify-content: center;
    gap: 10px;
    font-weight: 700;
    font-size: 40px;
    letter-spacing: 1px;
    line-height: 1;
  }
  .wordmark__square { width: 16px; height: 16px; background: currentColor; }
  .card--front .wordmark { top: 68px; }
  .card--back .wordmark { top: 90px; }

  .identity {
    position: absolute;
    top: 184px;
    right: 256px;
    text-align: right;
  }
  .identity__name { font-size: 17px; font-weight: 500; letter-spacing: 0.3px; line-height: 1.15; }
  .identity__role { font-size: 13px; font-weight: 500; color: var(--ink-soft); line-height: 1.5; }

  .divider {
    position: absolute;
    left: 218px;
    top: 184px;
    width: 1px;
    height: 42px;
    background: var(--rule);
  }

  .contact {
    position: absolute;
    left: 233px;
    top: 186px;
    list-style: none;
    font-size: 13px;
    color: var(--ink-mid);
  }
  .contact__item { display: flex; align-items: center; gap: 7px; height: 19px; }
  .contact__icon { width: 10px; height: 12px; flex: none; }

  .url-line {
    position: absolute;
    left: 0; right: 0;
    top: 185px;
    text-align: center;
    font-size: 10px;
    font-weight: 600;
    letter-spacing: 2.4px;
  }
</style>
</head>
<body>
  <section class="card card--front" aria-label="Card front">
    <div class="wordmark"><span class="wordmark__square"></span>LUMADRIFT</div>
    <div class="identity">
      <p class="identity__name">MARCUS HALE</p>
      <p class="identity__role">CEO/FOUNDER</p>
    </div>
    <div class="divider"></div>
    <ul class="contact">
      <li class="contact__item">
        <svg class="contact__icon" viewBox="0 0 10 12" aria-hidden="true">
          <rect x="1.5" y="0.5" width="7" height="11" rx="1.2" fill="none" stroke="#1c1c1c" stroke-width="1.3"/>
          <rect x="4" y="9" width="2" height="1" fill="#1c1c1c"/>
        </svg>
        <span>(318) 4207265518</span>
      </li>
      <li class="contact__item">
        <svg class="contact__icon" viewBox="0 0 12 12" aria-hidden="true">
          <circle cx="6" cy="6" r="5.5" fill="#1c1c1c"/>
          <path d="M3 4 Q5 3 6 5 T9 7 M4 8 Q5 7 6 9" stroke="#fbfbfb" stroke-width="1" fill="none"/>
        </svg>
        <span>www.lumadrift.com</span>
      </li>
    </ul>
  </section>

  <section class="card card--back" aria-label="Card back">
    <div class="wordmark"><span class="wordmark__square"></span>LUMADRIFT</div>
    <p class="url-line">WWW.LUMADRIFT.COM</p>
  </section>
</body>
</html>
```